Web Design For Manufacturing And Outsourcing Company

Pick up the pieces from our previous developer and help us complete our website.

5 pages - Home,Machining,Sourcing,About Us, and Contact

Attached you will find screen shots of previous direction but we're open to new ideas.

We can provide all text and images needed.

Thanks!

Number of Pages Required

5+ page

```html
<!DOCTYPE html>
<html lang="en">
<head>
<meta charset="utf-8">
<title>Kestrel Industries</title>
<link href="https://fonts.googleapis.com/css2?family=Oswald:wght@400;500;600&family=Open+Sans:wght@400;600&display=swap" rel="stylesheet">
<style>
:root{
  --orange:#e8501c;
  --orange-soft:#f9c4ad;
  --orange-pale:#fdebe3;
  --dark:#1f1f1f;
  --hero-top:#2f2f2f;
  --hero-bottom:#191919;
  --grey:#f1f1f1;
  --grey-mid:#d9d9d9;
  --ink:#2a2a2a;
  --text:#555;
  --white:#fff;
  --line:#c4c4c4;
}
*{margin:0;padding:0;box-sizing:border-box}
html,body{width:1200px;height:3888px;overflow:hidden}
body{font-family:"Open Sans",Arial,sans-serif;color:var(--text);background:var(--white);position:relative}
h1,h2,.nav a,.btn,.logo{font-family:"Oswald","Arial Narrow",sans-serif}
.site-header{position:absolute;top:0;left:0;width:1200px;height:98px;background:rgba(22,22,22,.92);z-index:2}
.logo{position:absolute;left:112px;top:30px;display:flex;align-items:center;gap:12px;color:var(--white);font-weight:500;font-size:17px;letter-spacing:3px}
.logo-mark{width:36px;height:36px;background:var(--orange)}
.nav{position:absolute;right:112px;top:36px;display:flex;gap:38px;align-items:center}
.nav a{color:var(--white);text-decoration:none;font-size:16px;font-weight:500;letter-spacing:.5px}
.nav a.active{color:var(--orange)}
.hero{position:absolute;top:0;left:0;width:1200px;height:640px;background:radial-gradient(circle at 82% 38%,#4a4a4a 0%,#383838 22%,var(--hero-top) 45%,var(--hero-bottom) 100%)}
.hero h1{position:absolute;top:225px;width:100%;text-align:center;color:var(--white);font-weight:500;font-size:54px;line-height:78px;letter-spacing:.5px}
.panel{position:absolute;top:640px;height:780px;text-align:center}
.panel-machining{left:0;width:598px;background:var(--orange);color:var(--white)}
.panel-sourcing{left:598px;width:602px;background:var(--grey);color:var(--text)}
.panel svg{position:absolute;top:66px;left:50%;margin-left:-160px}
.panel h2{position:absolute;top:432px;width:100%;font-size:44px;font-weight:500;letter-spacing:1px}
.panel-machining h2{color:var(--white)}
.panel-sourcing h2{color:var(--ink)}
.panel p{position:absolute;top:514px;left:50%;transform:translateX(-50%);width:470px;font-size:15px;line-height:28px}
.btn{display:inline-block;height:56px;line-height:52px;padding:0 44px;border:2px solid var(--orange);border-radius:28px;color:var(--orange);font-size:16px;font-weight:500;letter-spacing:1px;text-decoration:none;background:var(--white);white-space:nowrap}
.panel .btn{position:absolute;top:634px;left:50%;transform:translateX(-50%)}
.panel-machining .btn{background:transparent;border-color:var(--white);color:var(--white)}
.about{position:absolute;top:1420px;left:0;width:1200px;height:726px;text-align:center}
.about h2{position:absolute;top:100px;width:100%;font-size:44px;font-weight:500;color:var(--ink);letter-spacing:1px}
.about p{position:absolute;top:192px;left:50%;transform:translateX(-50%);width:805px;font-size:14px;line-height:28px}
.values{position:absolute;top:343px;left:306px;display:flex;gap:107px}
.value{width:124px;text-align:center}
.value-icon{width:124px;height:124px;border:2px solid var(--line);border-radius:50%;display:flex;align-items:center;justify-content:center}
.value-icon i{display:block;width:62px;height:62px;border-radius:50%;background:radial-gradient(circle at 40% 35%,var(--orange-pale) 0%,var(--orange-soft) 60%,var(--orange) 130%)}
.value span{display:block;margin-top:18px;font-size:19px;color:var(--ink);white-space:nowrap;margin-left:-20px;width:164px}
.about .btn{position:absolute;top:560px;left:50%;transform:translateX(-50%)}
.feature{position:absolute;left:0;width:1200px;height:534px}
.feature-machining{top:2146px;background:var(--grey)}
.feature-sourcing{top:2680px;background:var(--grey)}
.photo{position:absolute;top:0;height:534px}
.photo-lathe{left:0;width:598px;background:
  radial-gradient(ellipse 60% 20% at 50% 55%,rgba(235,235,235,.85) 0%,rgba(180,180,180,.4) 55%,rgba(0,0,0,0) 100%),
  linear-gradient(125deg,#2c2f33 0%,#55595e 25%,#9a9893 45%,#c39a58 65%,#7a5a30 82%,#2a2017 100%)}
.photo-network{left:601px;width:599px;background:
  radial-gradient(circle at 50% 45%,rgba(225,230,235,.9) 0%,rgba(160,175,190,.6) 14%,rgba(0,0,0,0) 28%),
  radial-gradient(ellipse at 50% 85%,#8a6e5c 0%,rgba(138,110,92,0) 45%),
  radial-gradient(circle at 50% 40%,#5f82a6 0%,#3a6188 45%,#1f3f63 100%)}
.feature-text{position:absolute;top:0;width:480px}
.feature-machining .feature-text{left:661px}
.feature-sourcing .feature-text{left:111px}
.feature h2{margin-top:64px;font-size:44px;font-weight:500;color:var(--ink);letter-spacing:1px}
.feature p{margin-top:22px;font-size:14px;line-height:27px;width:410px}
.feature p+p{margin-top:22px}
.feature .btn{margin-top:34px;padding:0 30px}
.cta{position:absolute;top:3214px;left:0;width:1200px;height:376px;background:var(--orange);text-align:center}
.cta h2{position:absolute;top:72px;width:100%;color:var(--white);font-size:44px;font-weight:500;line-height:62px;letter-spacing:1px}
.cta .btn{position:absolute;top:236px;left:50%;transform:translateX(-50%);background:transparent;border-color:var(--white);color:var(--white);padding:0 50px;height:62px;line-height:58px;border-radius:31px}
.site-footer{position:absolute;top:3590px;left:0;width:1200px;height:298px;text-align:center}
.social{position:absolute;top:104px;left:50%;transform:translateX(-50%);display:flex;gap:8px}
.social span{width:52px;height:52px;border:2px solid var(--line);border-radius:50%;display:flex;align-items:center;justify-content:center}
.social span i{display:block;width:14px;height:14px;border-radius:50%;background:var(--orange)}
.footer-links{position:absolute;top:186px;width:100%;font-size:13px;color:var(--text)}
.footer-links a{color:var(--text);text-decoration:none;margin:0 12px}
.copyright{position:absolute;top:228px;width:100%;font-size:13px}
</style>
</head>
<body>
<section class="hero">
  <h1>A SINGLE POINT OF CONTACT FOR ALL<br>YOUR PROCUREMENT NEEDS</h1>
</section>
<header class="site-header">
  <div class="logo"><span class="logo-mark"></span>KESTREL INDUSTRIES</div>
  <nav class="nav">
    <a href="#" class="active">HOME</a>
    <a href="#">MACHINING CAPABILITIES</a>
    <a href="#">SOURCING</a>
    <a href="#">CONTACT US</a>
    <svg width="18" height="18" viewBox="0 0 18 18" aria-label="Search"><circle cx="7.5" cy="7.5" r="5.5" fill="none" stroke="#fff" stroke-width="2.5"/><line x1="11.5" y1="11.5" x2="16.5" y2="16.5" stroke="#fff" stroke-width="2.5"/></svg>
  </nav>
</header>

<section class="panel panel-machining">
  <svg width="320" height="330" viewBox="0 0 320 330" role="img" aria-label="Machining icons: robotic arm, blueprint and production line">
    <defs>
      <radialGradient id="tintWarm" cx="50%" cy="45%" r="55%">
        <stop offset="0" stop-color="#fdebe3"/>
        <stop offset=".7" stop-color="#f9c4ad"/>
        <stop offset="1" stop-color="#f29a76"/>
      </radialGradient>
    </defs>
    <line x1="160" y1="80" x2="80" y2="240" stroke="#fff" stroke-width="4"/>
    <line x1="160" y1="80" x2="240" y2="240" stroke="#fff" stroke-width="4"/>
    <line x1="80" y1="240" x2="240" y2="240" stroke="#fff" stroke-width="4"/>
    <g>
      <circle cx="160" cy="80" r="74" fill="none" stroke="#fff" stroke-width="3"/>
      <circle cx="160" cy="80" r="68" fill="#fff"/>
      <circle cx="160" cy="80" r="44" fill="url(#tintWarm)"/>
      <circle cx="80" cy="240" r="74" fill="none" stroke="#fff" stroke-width="3"/>
      <circle cx="80" cy="240" r="68" fill="#fff"/>
      <circle cx="80" cy="240" r="44" fill="url(#tintWarm)"/>
      <circle cx="240" cy="240" r="74" fill="none" stroke="#fff" stroke-width="3"/>
      <circle cx="240" cy="240" r="68" fill="#fff"/>
      <circle cx="240" cy="240" r="44" fill="url(#tintWarm)"/>
    </g>
  </svg>
  <h2>MACHINING</h2>
  <p>Whether prototype, quick-turn, short or medium run production, our in-house capabilities can help you with any machining needs you may have.</p>
  <a href="#" class="btn">LEARN MORE</a>
</section>

<section class="panel panel-sourcing">
  <svg width="320" height="330" viewBox="0 0 320 330" role="img" aria-label="Sourcing icons: checklist, planning board and delivery truck">
    <defs>
      <radialGradient id="tintCool" cx="50%" cy="45%" r="55%">
        <stop offset="0" stop-color="#f7f7f7"/>
        <stop offset=".65" stop-color="#e2e2e2"/>
        <stop offset="1" stop-color="#f3b8a0"/>
      </radialGradient>
    </defs>
    <line x1="160" y1="80" x2="80" y2="240" stroke="#d0d0d0" stroke-width="4"/>
    <line x1="160" y1="80" x2="240" y2="240" stroke="#d0d0d0" stroke-width="4"/>
    <line x1="80" y1="240" x2="240" y2="240" stroke="#d0d0d0" stroke-width="4"/>
    <circle cx="160" cy="80" r="72" fill="#fff" stroke="#d0d0d0" stroke-width="4"/>
    <circle cx="160" cy="80" r="44" fill="url(#tintCool)"/>
    <circle cx="80" cy="240" r="72" fill="#fff" stroke="#d0d0d0" stroke-width="4"/>
    <circle cx="80" cy="240" r="44" fill="url(#tintCool)"/>
    <circle cx="240" cy="240" r="72" fill="#fff" stroke="#d0d0d0" stroke-width="4"/>
    <circle cx="240" cy="240" r="44" fill="url(#tintCool)"/>
  </svg>
  <h2>SOURCING</h2>
  <p>We offer a One Stop Shop solution by leveraging existing relationships and supply base knowledge to source hard to locate items, components and assemblies at the lowest cost.</p>
  <a href="#" class="btn">LEARN MORE</a>
</section>

<section class="about">
  <h2>ABOUT US</h2>
  <p>We are committed to consistently exceeding customer expectations by providing products, services and sourcing solutions of the highest standard of quality. With our streamlined processes our method is efficient, provides value and ensures on time delivery. Our success is based on continuously improving the efficiencies and effectiveness of our products, processes, and quality management systems.</p>
  <div class="values">
    <div class="value"><div class="value-icon" role="img" aria-label="Teamwork icon"><i></i></div><span>Teamwork</span></div>
    <div class="value"><div class="value-icon" role="img" aria-label="Handshake icon"><i></i></div><span>Respect</span></div>
    <div class="value"><div class="value-icon" role="img" aria-label="Gratitude icon"><i></i></div><span>Gratitude</span></div>
  </div>
  <a href="#" class="btn">LEARN MORE</a>
</section>

<section class="feature feature-machining">
  <div class="photo photo-lathe" role="img" aria-label="Photo of a metal part being turned on a lathe"></div>
  <div class="feature-text">
    <h2>MACHINING</h2>
    <p>Founded by a third generation machine shop owner, obsessed with streamlining the manufacturing process from start to finish.</p>
    <p>Kestrel Industries brings their machining knowledge to the table every day working closely with our customers to put value into each part we produce. Working as a strategic partner, Kestrel Industries is able to deliver precision.</p>
    <a href="#" class="btn">VIEW OUR EQUIPMENT LIST</a>
  </div>
</section>

<section class="feature feature-sourcing">
  <div class="feature-text">
    <h2>SOURCING</h2>
    <p>Over the years we identified the need to provide one stop services to purchasing departments. We have built an extensive network of hard to find products, machining specialists and leveraging open machine time to provide the most economical alternatives to our customers. We have developed a specialized method to supply our customers with the benefits they desire.</p>
    <a href="#" class="btn">VIEW OUR EQUIPMENT LIST</a>
  </div>
  <div class="photo photo-network" role="img" aria-label="Photo of hands joining puzzle pieces over a network of connected people"></div>
</section>

<section class="cta">
  <h2>CONTACT US TODAY WITH YOUR<br>MACHINING OR SOURCING NEEDS!</h2>
  <a href="#" class="btn">GET IN TOUCH</a>
</section>

<footer class="site-footer">
  <div class="social" aria-label="Social links">
    <span role="img" aria-label="Social link"><i></i></span>
    <span role="img" aria-label="Social link"><i></i></span>
    <span role="img" aria-label="Video channel link"><i></i></span>
    <span role="img" aria-label="Photo channel link"><i></i></span>
  </div>
  <div class="footer-links">
    <a href="#">Help</a>|<a href="#">FAQ</a>|<a href="#">Support</a>|<a href="#">Sitemap</a>|<a href="#">Terms Of Use</a>|<a href="#">Privacy Statement</a>
  </div>
  <div class="copyright">Kestrel Industries &copy; 2019 All rights reserved.</div>
</footer>
</body>
</html>
```